Communication and Marketing agency needs a new presentation card

We are a group of communication and marketing agencies specialized in companies that are in the logistics and industrial sector. The head agency is TELVANO Grupo and the group consists of 4 agencies: TELVANO Media, TELVANO Digital, TELVANO Research and DifundeEnPantalla. We hace 4 offices in Spain (Madrid, Barcelona, Valencia and Murcia). We are looking for a clean and attractive design that transmits our experience, brand presence in the market and knowledge to those who receive the card.It has to maintain the colors of the logo that is attached.
Target Market(s)
logistics and industrial sector
Marketing department
Contact Information for Business Card
Clean and attractive design

```html
<!DOCTYPE html>
<html lang="en">
<head>
<meta charset="utf-8">
<title>TELVANO Media — Business Card</title>
<link href="https://fonts.googleapis.com/css2?family=Open+Sans:wght@400;600&display=swap" rel="stylesheet">
<style>
  :root{
    --stage:#25272c;
    --paper:#ffffff;
    --brand-red:#b31b27;
    --ink-grey:#55524f;
    --name-grey:#4a4745;
    --on-red:#ffffff;
  }
  html,body{margin:0;padding:0;overflow:hidden;}
  body{width:1200px;height:960px;background:var(--stage);font-family:"Open Sans",Arial,sans-serif;position:relative;}
  .card{position:absolute;left:250px;width:700px;height:400px;background:var(--paper);overflow:hidden;box-shadow:0 18px 40px rgba(0,0,0,.45);}
  .card--front{top:60px;}
  .card--back{top:500px;}
  .card__shape{position:absolute;inset:0;width:100%;height:100%;}
  .wordmark{position:absolute;color:var(--brand-red);font-weight:600;letter-spacing:2px;white-space:nowrap;}
  .card--front .wordmark{left:0;right:0;top:130px;text-align:center;font-size:52px;}
  .card--back .wordmark{right:50px;top:48px;font-size:40px;}
  .front__web{position:absolute;left:300px;top:322px;color:var(--on-red);font-size:15px;letter-spacing:.5px;transform:rotate(-14deg);transform-origin:left center;}
  .contact{position:absolute;color:var(--on-red);font-size:16px;line-height:1.4;white-space:nowrap;}
  .contact__name{position:absolute;left:262px;top:248px;color:var(--name-grey);font-size:21px;letter-spacing:2px;text-transform:uppercase;white-space:nowrap;}
  .contact__role{left:262px;top:279px;}
  .contact__divider{position:absolute;left:490px;top:252px;width:1px;height:56px;background:rgba(255,255,255,.45);}
  .contact__address{left:505px;top:254px;}
  .contact__phone{left:130px;top:325px;}
  .contact__email{left:130px;top:349px;}
  .contact__web{left:400px;top:349px;letter-spacing:.5px;}
</style>
</head>
<body>
  <section class="card card--front" aria-label="Card front">
    <svg class="card__shape" viewBox="0 0 700 400" preserveAspectRatio="none" aria-hidden="true">
      <path d="M0,345 Q360,300 700,170 L700,250 Q360,380 0,400 Z" fill="var(--brand-red)"/>
    </svg>
    <div class="wordmark">TELVANO Media</div>
    <div class="front__web">www.telvanomedia.com</div>
  </section>

  <section class="card card--back" aria-label="Card back">
    <svg class="card__shape" viewBox="0 0 700 400" preserveAspectRatio="none" aria-hidden="true">
      <path d="M0,372 Q300,170 700,110 L700,400 L0,400 Z" fill="var(--ink-grey)"/>
      <path d="M0,382 Q300,180 700,120 L700,400 L0,400 Z" fill="var(--brand-red)"/>
    </svg>
    <div class="wordmark">TELVANO Media</div>
    <div class="contact__name">Marcela Ortun</div>
    <div class="contact contact__role">Managing Director</div>
    <div class="contact__divider"></div>
    <div class="contact contact__address">1480 Harbor Lane<br>Port Alden, LA 70999</div>
    <div class="contact contact__phone">555-014-(2290)</div>
    <div class="contact contact__email">info@telvanomedia.com</div>
    <div class="contact contact__web">WWW.TELVANOMEDIA.COM</div>
  </section>
</body>
</html>
```